Red Kite Pictures BIz Card

This will be a biz card for our independent film company
RED KITE PICTURES

we have a logo and i need to figure out how to post it to you!

Here is the info we need on the card:

LOGO

doralise vantkamp (lower case!)
dV@RedKitePictures.example
555-284-7163

Red Kite Pictures, LLC
www.RedKitePictures.example

frames worth keeping (tagline)

Target Market(s)

adults in the entertainment industry in USA.
need something creative feeling, a bit funky, not to overt.
something eye catchy that people will be inclined to keep.

ask me any questions you have!

Requirements
Must have
• good looking! clean and easy to get the contact info. not too busy.
Nice to have
• love the cards where the design is "continued" on the back side.

perhaps the tag and logo on the back side?!?

open to ideas!
Should not have
• nothing "cartoonish"

```html
<!DOCTYPE html>
<html lang="en">
<head>
<meta charset="UTF-8">
<title>Red Kite Pictures – Business Card</title>
<link rel="stylesheet" href="https://fonts.googleapis.com/css2?family=Questrial&display=swap">
<style>
  :root {
    --ink-black: #1f1f1f;
    --paper-white: #ffffff;
    --kite-red: #e2231a;
    --text-dark: #222222;
    --card-edge: #e4e4e4;
    --font-main: "Questrial", "Century Gothic", sans-serif;
  }
  * { margin: 0; padding: 0; box-sizing: border-box; }
  html, body {
    width: 1200px;
    height: 900px;
    overflow: hidden;
    background: var(--paper-white);
    font-family: var(--font-main);
  }
  .canvas {
    position: relative;
    width: 1200px;
    height: 900px;
  }
  .card {
    position: absolute;
    width: 550px;
    height: 358px;
  }
  .card--front {
    left: 290px;
    top: 66px;
    background: var(--ink-black);
  }
  .card--back {
    left: 300px;
    top: 480px;
    width: 540px;
    height: 356px;
    background: var(--paper-white);
    border: 1px solid var(--card-edge);
  }
  .wordmark {
    position: absolute;
    display: flex;
    align-items: center;
    gap: 12px;
    white-space: nowrap;
  }
  .wordmark__dot {
    flex: none;
    border-radius: 50%;
    background: var(--kite-red);
  }
  .wordmark__name { line-height: 1; }
  .tagline {
    position: absolute;
    color: var(--kite-red);
    white-space: nowrap;
    line-height: 1;
  }
  /* front */
  .card--front .wordmark { right: 40px; top: 150px; }
  .card--front .wordmark__dot { width: 26px; height: 26px; }
  .card--front .wordmark__name { color: var(--paper-white); font-size: 48px; letter-spacing: -0.5px; }
  .card--front .tagline { right: 42px; top: 206px; font-size: 19px; }
  /* back */
  .card--back .wordmark { right: 18px; top: 34px; gap: 8px; }
  .card--back .wordmark__dot { width: 15px; height: 15px; }
  .card--back .wordmark__name { color: var(--text-dark); font-size: 27px; letter-spacing: -0.3px; }
  .card--back .tagline { right: 20px; top: 70px; font-size: 13px; color: var(--text-dark); }
  .contact {
    position: absolute;
    left: 24px;
    color: var(--kite-red);
    line-height: 1.35;
  }
  .contact::before {
    content: "";
    position: absolute;
    left: -14px;
    top: 9px;
    width: 8px;
    height: 8px;
    border-radius: 50%;
    background: var(--text-dark);
  }
  .contact--person { top: 142px; }
  .contact--company { top: 214px; }
  .contact--company::before { top: 4px; }
  .contact__name { font-size: 27px; line-height: 1.05; margin-bottom: 4px; }
  .contact__line { font-size: 12px; }
  .site-link {
    position: absolute;
    right: 22px;
    bottom: 18px;
    display: flex;
    align-items: center;
    gap: 8px;
    color: var(--kite-red);
    font-size: 19px;
    line-height: 1;
  }
  .site-link__dot {
    flex: none;
    width: 9px;
    height: 9px;
    border-radius: 50%;
    background: var(--text-dark);
  }
</style>
</head>
<body>
  <main class="canvas">
    <section class="card card--front" aria-label="Card front">
      <div class="wordmark">
        <span class="wordmark__dot"></span>
        <span class="wordmark__name">Red Kite Pictures</span>
      </div>
      <p class="tagline">frames worth keeping</p>
    </section>

    <section class="card card--back" aria-label="Card back">
      <div class="wordmark">
        <span class="wordmark__dot"></span>
        <span class="wordmark__name">Red Kite Pictures</span>
      </div>
      <p class="tagline">frames worth keeping</p>

      <div class="contact contact--person">
        <p class="contact__name">doralise vantkamp</p>
        <p class="contact__line">dV@RedKitePictures.example</p>
        <p class="contact__line">555-284-7163</p>
      </div>

      <div class="contact contact--company">
        <p class="contact__line">Red Kite Pictures, LLC</p>
        <p class="contact__line">www.RedKitePictures.example</p>
      </div>

      <p class="site-link">
        <span class="site-link__dot"></span>
        <span>www.RedKitePictures.example</span>
      </p>
    </section>
  </main>
</body>
</html>
```